Im open to ideas.. I was thinking on my business cards aswell as my logo. a place for my name. email. phone number and abn..

ive attched a file with my business logo. which i dont love the colours.. i was think a dark background with charcoal letters so something along those colour schumes but im open to ideas..

BRM Constructions

```html
<!DOCTYPE html>
<html lang="en">
<head>
<meta charset="utf-8">
<title>BRM Constructions – Business Card</title>
<link rel="stylesheet" href="https://fonts.googleapis.com/css2?family=Michroma&family=Roboto:wght@400;700&display=swap">
<style>
  :root {
    --backdrop: #1c1c1c;
    --card: #f1f1f1;
    --card-edge: #dcdcdc;
    --brand-red: #e0141c;
    --deep-red: #a80d12;
    --charcoal: #222222;
    --ink: #2a2a2a;
    --white: #ffffff;
  }
  * { box-sizing: border-box; margin: 0; padding: 0; }
  html, body {
    width: 1200px; height: 873px; overflow: hidden;
    background: var(--backdrop);
  }
  .card {
    position: absolute; left: 180px; top: 196px;
    width: 840px; height: 480px;
    background: linear-gradient(160deg, #fafafa, var(--card) 60%, #e6e6e6);
    border-radius: 22px;
    border: 1px solid var(--card-edge);
    overflow: hidden;
    font-family: "Michroma", sans-serif;
    color: var(--ink);
  }
  .brand {
    position: absolute; top: 78px; left: 0; width: 100%;
    display: flex; justify-content: center; align-items: center; gap: 16px;
  }
  .brand-mark {
    width: 22px; height: 22px; background: var(--brand-red);
  }
  .brand-name {
    font-family: "Michroma", sans-serif;
    font-size: 34px; color: var(--charcoal); letter-spacing: 1px;
  }
  .band {
    position: absolute; left: 0; top: 150px; width: 100%; height: 150px;
    background: var(--brand-red);
    display: flex; flex-direction: column; align-items: center; justify-content: center; gap: 18px;
  }
  .identity {
    font-family: "Roboto", sans-serif; color: var(--white);
    display: flex; align-items: center; gap: 12px;
  }
  .identity .person { font-size: 26px; font-weight: 700; }
  .identity .divider { width: 1px; height: 26px; background: rgba(255,255,255,.6); }
  .identity .role { font-size: 18px; font-weight: 400; }
  .website {
    font-family: "Roboto", sans-serif; font-weight: 700;
    font-size: 20px; color: var(--deep-red);
  }
  .contacts {
    position: absolute; left: 52px; top: 334px;
    list-style: none; display: flex; flex-direction: column; gap: 16px;
    font-size: 17px;
  }
  .contacts li { display: flex; align-items: center; gap: 18px; }
  .contacts svg { width: 22px; height: 22px; fill: var(--brand-red); flex: none; }
  .address {
    position: absolute; right: 48px; top: 334px;
    text-align: right; font-style: normal; font-size: 17px; line-height: 1.9;
    color: var(--charcoal);
  }
</style>
</head>
<body>
  <article class="card">
    <header class="brand">
      <span class="brand-mark"></span>
      <span class="brand-name">BRM CONSTRUCTIONS</span>
    </header>

    <section class="band">
      <p class="identity">
        <span class="person">Daniel R Moreno</span>
        <span class="divider"></span>
        <span class="role">Managing Partner</span>
      </p>
      <p class="website">www.brmbuildgroup.com</p>
    </section>

    <ul class="contacts">
      <li>
        <svg viewBox="0 0 24 24" aria-hidden="true"><path d="M3 9c0-3 4-5 9-5s9 2 9 5v2h-5V9H8v2H3z"/><path d="M5 13h14l1 7H4z"/><circle cx="12" cy="16.5" r="2" fill="#f1f1f1"/></svg>
        <span>+1 (555) 210-4836</span>
      </li>
      <li>
        <svg viewBox="0 0 24 24" aria-hidden="true"><path d="M7 2h10a2 2 0 0 1 2 2v16a2 2 0 0 1-2 2H7a2 2 0 0 1-2-2V4a2 2 0 0 1 2-2zm0 3v13h10V5z"/></svg>
        <span>+1 (555) 379-1524</span>
      </li>
      <li>
        <svg viewBox="0 0 24 24" aria-hidden="true"><path d="M2 5h20v14H2z"/><path d="M3 6l9 7 9-7" fill="none" stroke="#f1f1f1" stroke-width="1.6"/></svg>
        <span>dmoreno@brmbuildgroup.com</span>
      </li>
    </ul>

    <address class="address">
      18 Cedar Ridge Road<br>
      2nd Floor, Millbrook, ST 00000
    </address>
  </article>
</body>
</html>
```